Graphic Design Project

ok I have the artwork for my presentation folder, and I have the text to put on the folder, I need you to apply text to the folder and the single sheets, so inside the artwork is pictures to use, text to use. thank you so much ask me as many questions as you need
Updates

my girl forgot to upload the mock ups of the presentation folder and single sheets, my apologies please check updated files

Hey Guys this is a eazy project the artwork is done, the text is done, the pictures are done!, all you have to do is assemble the project, I even have mock up pictures of how project looks finished, I have made the money good so that you would not pass on this project because it is not that creative of a job!

Target Market(s)

Dr's and patients

Industry/Entity Type

Graphic Design

Requirements
Must have
• use the single sheet artwork to make as many single sheets as you need to use all of the text supplied
Should not have
• do not make this, so professional looking that it does not appeal to the patients

```html
<!DOCTYPE html>
<html lang="en">
<head>
<meta charset="UTF-8">
<title>Why Is Patient Education So Important</title>
<link href="https://fonts.googleapis.com/css2?family=Tinos:wght@400;700&display=swap" rel="stylesheet">
<style>
  :root {
    --backdrop: #e9e6e2;
    --sheet: #ffffff;
    --panel-grey: #d4d4d6;
    --panel-beige: #dbd3c3;
    --heading-brown: #8a4a22;
    --bullet-brown: #7a4426;
    --body-ink: #1d1d1d;
    --photo-warm: #b79a80;
    --photo-light: #e3d6c6;
  }
  * { margin: 0; padding: 0; box-sizing: border-box; }
  html, body {
    width: 1200px;
    height: 1000px;
    overflow: hidden;
    background: var(--backdrop);
  }
  .info-sheet {
    position: absolute;
    left: 256px;
    top: 66px;
    width: 686px;
    height: 886px;
    background: var(--sheet);
    box-shadow: 0 2px 10px rgba(0,0,0,0.12);
    overflow: hidden;
    font-family: "Tinos", "Times New Roman", serif;
  }
  .sheet-shapes {
    position: absolute;
    inset: 0;
    width: 686px;
    height: 886px;
  }
  .sheet-title {
    position: absolute;
    left: 55px;
    top: 66px;
    font-size: 24px;
    font-weight: 700;
    color: var(--heading-brown);
    letter-spacing: 0.2px;
    text-transform: uppercase;
  }
  .benefit-list {
    position: absolute;
    left: 62px;
    top: 119px;
    width: 620px;
    list-style: none;
  }
  .benefit-list li {
    position: relative;
    padding-left: 15px;
    font-size: 15.5px;
    line-height: 20px;
    color: var(--body-ink);
    margin-bottom: 17px;
  }
  .benefit-list li::before {
    content: "";
    position: absolute;
    left: 0;
    top: 6px;
    width: 8px;
    height: 8px;
    background: var(--bullet-brown);
    clip-path: polygon(0 15%, 100% 0, 100% 100%, 0 85%);
  }
</style>
</head>
<body>
  <article class="info-sheet">
    <svg class="sheet-shapes" viewBox="0 0 686 886" xmlns="http://www.w3.org/2000/svg">
      <defs>
        <linearGradient id="photo-tones" x1="0" y1="0" x2="1" y2="0">
          <stop offset="0" stop-color="var(--photo-warm)"/>
          <stop offset="0.35" stop-color="var(--photo-light)"/>
          <stop offset="0.62" stop-color="var(--panel-beige)"/>
          <stop offset="1" stop-color="var(--panel-beige)"/>
        </linearGradient>
      </defs>
      <path class="panel-main" fill="var(--panel-grey)"
            d="M0 0 H545 L686 40 V350 L612 626 Q604 652 578 645 L0 505 Z"/>
      <path class="panel-photo" fill="url(#photo-tones)" role="img"
            aria-label="Photo of a smiling elderly couple embracing"
            d="M0 535 L560 676 Q586 684 580 710 L545 886 H0 Z"/>
      <path class="panel-accent-beige" fill="var(--panel-beige)"
            d="M686 440 V775 L620 757 Q598 750 604 727 L673 462 Q678 446 686 440 Z"/>
      <path class="panel-accent-grey" fill="var(--panel-grey)"
            d="M686 808 L620 788 Q596 782 590 806 L570 886 H686 Z"/>
    </svg>

    <h1 class="sheet-title">Why Is Patient Education So Important??</h1>

    <ul class="benefit-list">
      <li>Patients have an improved understanding of their medication and over the counter interactions.</li>
      <li>Increased Compliance – Effective communication and patient education increases patient motivation to comply.</li>
      <li>Patient Outcomes – Patients are more likely to respond well to their treatment plan – fewer complications.</li>
      <li>Informed Consent – Patients feel you’ve provided the information they need.</li>
      <li>Utilization – More effective use of medical services – fewer unnecessary phone calls and visits.</li>
      <li>Satisfaction and referrals – Patients more likely to stay with your practice and refer other patients.</li>
      <li>Risk Management - Lower risk of malpractice when patients are more engaged, adherent, atisfied, and have realistic expectations.</li>
    </ul>
  </article>
</body>
</html>
```